Copper Lantern

Need a business card for our restaurant. Restaurant and Bar in the mountains of North Idaho. Rustic looking card

rustic design, wood and metal looking, primarily neutral colors

• Name, address, phone number, website, email address

```html
<!DOCTYPE html>
<html lang="en">
<head>
<meta charset="utf-8">
<title>Copper Lantern – Business Card</title>
<link rel="stylesheet" href="https://fonts.googleapis.com/css2?family=Montserrat:wght@400;600&display=swap">
<style>
  :root {
    --backdrop: #2b2b2b;
    --card: #121212;
    --card-edge: #1c1c1c;
    --ink: #f2f2f2;
    --ink-soft: #d6d6d6;
    --silver: #bdbdbd;
  }
  * { margin: 0; padding: 0; box-sizing: border-box; }
  html, body { width: 1200px; height: 874px; overflow: hidden; }
  body {
    background: var(--backdrop);
    font-family: "Montserrat", sans-serif;
    display: flex;
    flex-direction: column;
    align-items: center;
    justify-content: center;
    gap: 40px;
  }
  .card {
    width: 630px;
    height: 360px;
    background: var(--card);
    border: 1px solid var(--card-edge);
    border-radius: 18px;
    position: relative;
    color: var(--ink);
  }
  /* front */
  .card--front {
    display: flex;
    align-items: center;
    justify-content: center;
    gap: 18px;
  }
  .brand-mark {
    width: 34px; height: 34px;
    border: 2px solid currentColor;
    border-radius: 50%;
    flex: none;
  }
  .brand-name {
    font-weight: 600;
    letter-spacing: 0.14em;
    text-transform: uppercase;
  }
  .card--front .brand { color: var(--silver); display: flex; align-items: center; gap: 16px; }
  .card--front .brand-name { font-size: 30px; }

  /* back */
  .card--back .brand {
    position: absolute; left: 34px; top: 40px;
    display: flex; align-items: center; gap: 12px;
    color: var(--ink);
  }
  .card--back .brand-mark { width: 26px; height: 26px; }
  .card--back .brand-name { font-size: 19px; }
  .address {
    position: absolute; left: 46px; top: 150px;
    font-size: 16px; line-height: 1.35; color: var(--ink-soft);
  }
  .contacts {
    position: absolute; left: 34px; top: 228px;
    list-style: none; font-size: 16px; color: var(--ink-soft);
  }
  .contacts li { display: flex; align-items: center; gap: 10px; line-height: 1.65; }
  .contacts svg { width: 13px; height: 13px; fill: var(--ink-soft); flex: none; }
  .person {
    position: absolute; right: 44px; top: 236px;
    text-align: right;
  }
  .person-name { font-size: 25px; font-weight: 600; color: var(--ink); }
  .person-role { font-size: 15px; color: var(--ink-soft); margin-top: 2px; }
</style>
</head>
<body>
  <section class="card card--front">
    <div class="brand">
      <span class="brand-mark"></span>
      <span class="brand-name">Copper Lantern</span>
    </div>
  </section>

  <section class="card card--back">
    <div class="brand">
      <span class="brand-mark"></span>
      <span class="brand-name">Copper Lantern</span>
    </div>

    <p class="address">Your address, City<br>State, Zip 1234</p>

    <ul class="contacts">
      <li>
        <svg viewBox="0 0 16 16" aria-hidden="true"><path d="M3 1h3l1.5 4-2 1.2a9 9 0 0 0 4.3 4.3L11 8.5l4 1.5v3a2 2 0 0 1-2 2A13 13 0 0 1 1 3a2 2 0 0 1 2-2z"/></svg>
        123 456 789
      </li>
      <li>
        <svg viewBox="0 0 16 16" aria-hidden="true"><path d="M1 3h14v10H1z M1 3l7 6 7-6" fill="none" stroke="#d6d6d6" stroke-width="1.6"/></svg>
        info@yourgmail.com
      </li>
      <li>
        <svg viewBox="0 0 16 16" aria-hidden="true"><circle cx="8" cy="8" r="6.5" fill="none" stroke="#d6d6d6" stroke-width="1.6"/><path d="M1.5 8h13M8 1.5c-3 3.5-3 9.5 0 13M8 1.5c3 3.5 3 9.5 0 13" fill="none" stroke="#d6d6d6" stroke-width="1.2"/></svg>
        www.yourwebsite.com
      </li>
    </ul>

    <div class="person">
      <p class="person-name">Owen Harrow</p>
      <p class="person-role">Managing Director</p>
    </div>
  </section>
</body>
</html>
```